Birchline Septic Solutions

Would like to see some single sided ones but would also like to see some double sided with one sided only being the logo. Owners name is Colin Vandro. Phone number is 555-214-0387
Services are pumping, inspections, installs, and repairs

Contact Information for Business Card

555-241-0387 Colin Vandro Alderbrook, OH

```html
<!DOCTYPE html>
<html lang="en">
<head>
<meta charset="utf-8">
<title>Birchline Septic Solutions – Business Card</title>
<link href="https://fonts.googleapis.com/css2?family=Open+Sans:wght@400;600;800&display=swap" rel="stylesheet">
<style>
  :root {
    --page-bg: #e4e6ea;
    --card-dark: #0e0f11;
    --card-mid: #1c1d20;
    --card-edge: #34353a;
    --teal: #2a9a99;
    --teal-deep: #1f7b7c;
    --white-soft: #eef0f2;
    --name-light: #c9ccd8;
    --lavender: #8a8fb8;
    --service-grey: #8d8f98;
  }
  * { margin: 0; padding: 0; box-sizing: border-box; }
  html, body {
    width: 1200px; height: 779px; overflow: hidden;
    background: var(--page-bg);
    font-family: "Open Sans", Arial, sans-serif;
  }
  .card {
    position: absolute; left: 50px; top: 87px;
    width: 1100px; height: 605px;
    overflow: hidden;
    background:
      radial-gradient(ellipse 420px 520px at 330px 220px, rgba(90,92,98,0.45), transparent 70%),
      linear-gradient(100deg, var(--card-edge) 0%, var(--card-mid) 30%, var(--card-dark) 55%, var(--card-mid) 100%);
  }
  .edge-decoration {
    position: absolute; left: 0; top: 0;
    width: 175px; height: 605px;
    background: linear-gradient(90deg, rgba(20,21,23,0.9) 0%, rgba(40,41,45,0.55) 60%, transparent 100%);
  }
  .brand {
    position: absolute; right: 38px; top: 120px;
    width: 440px; text-align: center;
    color: var(--white-soft); font-weight: 800;
  }
  .brand-mark {
    display: inline-block; width: 22px; height: 22px;
    background: var(--teal); margin-bottom: 14px;
  }
  .brand-name { font-size: 78px; line-height: 1; letter-spacing: 1px; }
  .brand-sub { font-size: 23px; letter-spacing: 9px; margin-top: 10px; text-transform: uppercase; }
  .contact {
    position: absolute; right: 34px; top: 318px;
    text-align: right;
  }
  .contact-name { font-size: 46px; font-weight: 600; line-height: 1.15; }
  .contact-name .first { color: var(--teal); }
  .contact-name .last { color: var(--name-light); }
  .contact-city { font-size: 28px; color: var(--lavender); letter-spacing: 1px; margin-top: 2px; }
  .contact-phone { font-size: 28px; color: var(--lavender); letter-spacing: 1px; margin-top: 4px; display: flex; align-items: center; justify-content: flex-end; gap: 12px; }
  .accent-bar {
    position: absolute; right: 0; top: 322px;
    width: 17px; height: 110px; background: var(--teal-deep);
  }
  .services-pill {
    position: absolute; left: 461px; top: 491px;
    width: 178px; height: 38px; border-radius: 50%;
    background: radial-gradient(ellipse at center, var(--teal) 30%, var(--teal-deep) 100%);
    color: #d8eaea; font-size: 25px; font-weight: 600;
    display: flex; align-items: center; justify-content: center;
  }
  .services-list {
    position: absolute; left: 180px; top: 530px;
    display: flex; gap: 14px; list-style: none;
    font-size: 29px; color: var(--service-grey);
  }
  .services-list li { display: flex; align-items: center; gap: 14px; }
  .services-list li::before {
    content: ""; width: 18px; height: 18px; border-radius: 50%;
    background: var(--teal-deep);
  }
</style>
</head>
<body>
  <div class="card">
    <div class="edge-decoration" role="img" aria-label="Faint embossed pine trees and mountain ridge along the left edge"></div>

    <div class="brand">
      <span class="brand-mark"></span>
      <div class="brand-name">Birchline</div>
      <div class="brand-sub">Septic Solutions</div>
    </div>

    <div class="contact">
      <div class="contact-name"><span class="first">Colin</span> <span class="last">Vandro</span></div>
      <div class="contact-city">Alderbrook, OH</div>
      <div class="contact-phone">555-241-0387
        <svg width="24" height="24" viewBox="0 0 24 24" aria-hidden="true"><path d="M6.6 10.8a15.1 15.1 0 0 0 6.6 6.6l2.2-2.2a1 1 0 0 1 1-.25 11.4 11.4 0 0 0 3.6.57 1 1 0 0 1 1 1V20a1 1 0 0 1-1 1A17 17 0 0 1 3 4a1 1 0 0 1 1-1h3.5a1 1 0 0 1 1 1c0 1.25.2 2.45.57 3.57a1 1 0 0 1-.25 1z" fill="none" stroke="#2a9a99" stroke-width="2"/></svg>
      </div>
    </div>
    <div class="accent-bar"></div>

    <div class="services-pill">SERVICES</div>
    <ul class="services-list">
      <li>Pumping</li>
      <li>Inspections</li>
      <li>Installs</li>
      <li>And Repairs</li>
    </ul>
  </div>
</body>
</html>
```